Investment Management Firm Power point template

Marrow Holdings is a real estate investment firm focused on buying commercial office and residential property in the UK. We produce powerpoint presentations for our Board of Directors, Investment Committee and also to external investors.

We are looking for a powerpoint design template which we can use for future presentations which provide a professional look and feel.

Our current website: http://www.marrowholdings.example.co.uk/

Target Market(s)

Institution Investors, Board of Directors, Professionals

Industry/Entity Type

Real Estate

Requirements
Must have
• Leverage off the current logo and colour scheme. However, does not have to purely rely on this colour scheme.
• - Title page
• - Content Page
• - Slide where graphs can be incorporated
• - Slide where photos can be incorporated
• - Slide of UK Map which can show where the property portfolio is currently located
• - Other slides incorporating smart art or other designs that can be used for future presentations
Nice to have
• An example of graphics that we would love to have in the powerpoint pack which we can easily edit has been attached

```html
<!DOCTYPE html>
<html lang="en">
<head>
<meta charset="utf-8">
<title>About Us – Marrow Holdings</title>
<link rel="stylesheet" href="https://fonts.googleapis.com/css2?family=Titillium+Web:wght@300;400;700&display=swap">
<style>
  :root {
    --brand-orange: #f7841a;
    --photo-light: #fba347;
    --photo-dark: #e3700a;
    --panel-fill: rgba(196, 92, 0, 0.42);
    --panel-edge: rgba(255, 214, 160, 0.55);
    --text-white: #ffffff;
  }
  * { margin: 0; padding: 0; box-sizing: border-box; }
  html, body { width: 1200px; height: 900px; overflow: hidden; }
  body { font-family: "Titillium Web", Arial, sans-serif; background: var(--brand-orange); }

  .slide {
    position: relative;
    width: 1200px;
    height: 900px;
    background: var(--brand-orange);
    overflow: hidden;
  }
  .slide-photo {
    position: absolute;
    left: 558px;
    top: 0;
    width: 642px;
    height: 900px;
    background: linear-gradient(160deg, var(--photo-light) 0%, var(--brand-orange) 45%, var(--photo-dark) 100%);
  }
  .slide-title {
    position: absolute;
    left: 50px;
    top: 26px;
    font-size: 40px;
    font-weight: 700;
    color: var(--text-white);
    letter-spacing: 0.2px;
  }
  .about-panel {
    position: absolute;
    left: 99px;
    top: 247px;
    width: 969px;
    height: 439px;
    background: var(--panel-fill);
    border: 1.5px solid var(--panel-edge);
    display: flex;
    flex-direction: column;
    justify-content: center;
    padding: 0 40px;
  }
  .about-panel p {
    color: var(--text-white);
    font-weight: 300;
    font-size: 21px;
    line-height: 36px;
    text-align: center;
  }
  .about-panel p + p { margin-top: 36px; }

  .brand-tag {
    position: absolute;
    left: 15px;
    top: 844px;
    width: 226px;
    height: 41px;
    border: 1.5px solid var(--text-white);
    display: flex;
    align-items: center;
    gap: 12px;
    padding-left: 10px;
  }
  .brand-mark {
    width: 22px;
    height: 22px;
    border: 1.5px solid var(--text-white);
  }
  .brand-name {
    color: var(--text-white);
    font-weight: 400;
    font-size: 23px;
    line-height: 1;
  }
</style>
</head>
<body>
  <main class="slide">
    <div class="slide-photo" role="img" aria-label="Upward view of a glass office tower, tinted orange"></div>

    <h1 class="slide-title">About Us</h1>

    <section class="about-panel">
      <p>While a property’s fundamentals are important to us, we put equal focus on the people who use and enjoy our spaces. The experience of being in our buildings — from design to atmosphere — is strategically planned. Functionality and efficiency are crucial and technology is in our DNA.</p>
      <p>With these fundamental characteristics in mind we strive to create businesses around our properties, enhancing their value and creating long-term operating platforms.</p>
      <p>As part of the Ashgrove Kendal Group we directly and indirectly benefit from the ecosystem of companies around us. Ashgrove Kendal brings unrivalled expertise in building successful, long-lasting businesses.</p>
    </section>

    <div class="brand-tag">
      <span class="brand-mark"></span>
      <span class="brand-name">Marrow Holdings</span>
    </div>
  </main>
</body>
</html>
```